Window Treatment business needs website redesigned.

We need a revamp and refresh of our current site www.velmarix.ca
Looking to attract very high end customer. It should be a very simple design with very little text. This site will be visited by prospective homeowners, designers, builders and architects. They should feel that they are dealing with a high-end product selection, where experience, customer service and unique product offering is the focus. The content will be to highlight our services and highlight the manufacturers we sell, using a few rich photos to highlight the products. We should NOT look like we are a very large company. It should NOT have discounts/savings buttons and many menus to choose from. We offer over 15 years experience to narrow the many market options, to provide the right technical solution.
We specialize in products that are not readily available on the market and specifically motorized systems for indoors and outdoors.
Our main suppliers are Kravenholt.com, Dimbrell.com
We carry our own locally manufactured product line of roller shades.
Main product pictures should be of roller shades, outdoor bug screens, awnings and outdoor pergolas.

Reason: I understand that Christmas is coming up real short and many people are extremely busy. If you have a CREATIVE gifting you still want to submit, I look forward to your idea!

Reason: Due to holiday season, we have not had sufficient time to review to make a final decision. Thank you for your patience!

Target Market(s)

High end home owners, designers, builders, architects

Industry/Entity Type

Contractor

Coding

Coded - Design and coding required

Number of Pages Required

3 page

Font styles to use
Sans Serif

Requirements
Must have
• Landing page with full size image like homepage of zolvane.it
• Products page that highlights products with simple product shot image, description and link to manufacturer.
• On main page a scrolling of customer reviews.
• I want a very simple, eye-catching, emotional image for homepage. It does not need to include any product image.
• An image that shows technology combining/meshing with hand craftsmanship.
• Focus is on design.
• http://www.zolvane.it/en/gallery is a great layout and design.
Nice to have
• Logo shape for icons and watermark should be used.
• Look like and have simple motion effects like quorix.com or telvarin.com
Should not have
• Generic/standard looking feel like bluppet.com or mecklorwindow.ca
• No use of green as background only subtle text.
• Lots of text and pages.

```html
<!DOCTYPE html>
<html lang="en">
<head>
<meta charset="utf-8">
<title>Lumavane – Window Treatment Solutions</title>
<link href="https://fonts.googleapis.com/css2?family=Lato:wght@400;700;900&display=swap" rel="stylesheet">
<style>
:root{
  --green:#5cb531;
  --ink:#1c1c1c;
  --grey:#6e6e6e;
  --light:#efefef;
  --band:#dcdcdc;
  --dark:#2e2e2e;
  --slate:#6f7773;
  --black:#111;
  --white:#fff;
}
*{box-sizing:border-box;margin:0;padding:0}
html,body{width:1200px;height:3492px;overflow:hidden}
body{font-family:'Lato',sans-serif;color:var(--ink);background:var(--white);position:relative}
section,header,footer{position:absolute;left:0;width:1200px}

/* Header + hero */
.hero{top:0;height:780px;background:linear-gradient(135deg,#f4f5f5 0%,#dfe3e3 45%,#c9cfcf 70%,#eef0f0 100%)}
.hero-photo{position:absolute;inset:0}
.topbar{position:absolute;top:0;left:0;width:1200px;height:120px;display:flex;align-items:center;justify-content:space-between;padding:0 70px}
.brand{display:flex;align-items:center;gap:14px}
.brand-mark{width:52px;height:52px;border-radius:50%;background:var(--dark)}
.brand-name{font-size:38px;font-weight:900;color:var(--dark)}
.brand-tag{display:block;font-size:13px;font-weight:400;color:var(--grey);margin-top:2px}
.nav{display:flex;gap:36px;list-style:none;font-size:15px;font-weight:700;color:var(--dark)}
.nav li.active{color:var(--green)}
.hero-title{position:absolute;left:80px;top:280px;font-size:60px;font-weight:900;line-height:1.08;color:var(--ink);letter-spacing:1px}

/* Welcome */
.welcome{top:760px;height:440px;background:var(--white);clip-path:polygon(0 20px,100% 0,100% 100%,0 100%)}
.welcome h2{position:absolute;left:80px;top:50px;font-size:58px;font-weight:900;line-height:1.05}
.welcome h2 span{color:var(--ink)}
.welcome p{position:absolute;left:80px;top:200px;width:380px;font-size:15px;line-height:1.6;color:var(--grey)}
.btn-outline{position:absolute;left:80px;top:320px;padding:12px 22px;border:2px solid var(--ink);border-radius:24px;font-size:14px;font-weight:700;display:flex;align-items:center;gap:10px}
.hex-cluster{position:absolute;left:600px;top:10px;width:500px;height:400px}

/* Products */
.products{top:1200px;height:150px;display:flex;justify-content:space-between;padding:0 80px;align-items:center}
.product{display:flex;align-items:center;gap:14px}
.product-icon{width:90px;height:90px}
.product-name{font-size:24px;font-weight:700;color:var(--green);line-height:1.1}
.product-name b{color:var(--dark)}

/* Gallery */
.gallery{top:1350px;height:700px;background:var(--band);clip-path:polygon(0 60px,100% 0,100% 100%,0 100%)}
.gallery h2{position:absolute;left:80px;top:140px;font-size:60px;font-weight:900;color:var(--green)}
.gallery .lead{position:absolute;left:80px;top:220px;width:330px;font-size:17px;font-weight:700;line-height:1.4}
.filters{position:absolute;left:80px;top:310px;width:330px;list-style:none;font-size:15px}
.filters li{padding:12px 14px;border:1px solid #aaa;margin-bottom:6px;background:var(--white)}
.filters li.active{background:var(--black);color:var(--white)}
.grid{position:absolute;left:478px;top:150px;width:642px;display:grid;grid-template-columns:repeat(3,1fr);gap:8px}
.grid div{height:190px}
.g1{background:linear-gradient(160deg,#b9814a,#6e5a3c)}
.g2{background:linear-gradient(160deg,#9ec3d8,#4e6d7c)}
.g3{background:linear-gradient(160deg,#c5cbcf,#5b636a)}
.g4{background:linear-gradient(160deg,#a46b3e,#4b5a3b)}
.g5{background:linear-gradient(160deg,#d8dcde,#7b858b)}
.g6{background:linear-gradient(160deg,#6f8fa8,#3b4855)}

/* Why */
.why{top:2000px;height:560px;background:linear-gradient(135deg,#3a3a3a,#1f1f1f 60%,#4a4a4a);clip-path:polygon(0 0,100% 60px,100% 100%,0 100%);color:var(--white)}
.why h2{position:absolute;left:80px;top:110px;font-size:60px;font-weight:900}
.why p{position:absolute;left:80px;top:250px;width:1040px;font-size:15px;line-height:1.6;color:#ddd}
.call{position:absolute;left:80px;top:420px;display:flex;align-items:center;gap:20px;font-size:28px;font-weight:900}
.call-icon{width:54px;height:54px}

/* Testimonial */
.testimonial{top:2560px;height:380px;background:linear-gradient(180deg,#f2f2f2,#e4e4e4);text-align:center}
.testimonial h2{position:absolute;top:20px;width:100%;font-size:56px;font-weight:900;color:var(--green);letter-spacing:1px}
.quote-mark{position:absolute;top:110px;width:100%;font-size:40px;font-weight:900}
.testimonial p{position:absolute;left:200px;top:165px;width:800px;font-size:15px;line-height:1.6;color:var(--grey)}
.testimonial .client{position:absolute;top:250px;width:100%;font-size:13px;font-weight:700}
.arrow{position:absolute;top:140px;width:56px;height:56px}
.arrow.prev{left:80px}.arrow.next{right:80px}

/* Quote + contact */
.contact{top:2940px;height:500px;background:var(--slate);color:var(--white)}
.scroll-badge{position:absolute;left:550px;top:2880px;width:100px;height:100px;z-index:2}
.contact h3{font-size:40px;font-weight:900}
.quote-form{position:absolute;left:80px;top:40px;width:480px}
.quote-form h3{margin-bottom:20px}
.row{display:flex;gap:10px;margin-bottom:12px}
.field{flex:1;height:36px;border:1px solid #e4e4e4;padding:8px 10px;font-size:13px}
.field.tall{height:150px}
.submit{display:inline-block;background:var(--green);color:var(--ink);font-weight:700;font-size:15px;padding:10px 24px;margin-top:4px}
.contact-side{position:absolute;left:640px;top:40px;width:480px}
.contact-side .intro{font-size:26px;line-height:1.35;margin-bottom:16px}
.contact-btn{display:inline-block;background:var(--green);color:var(--ink);font-weight:700;font-size:15px;padding:10px 24px;margin-bottom:26px}
.info{list-style:none;margin-top:20px;font-size:14px}
.info li{display:flex;gap:16px;align-items:flex-start;margin-bottom:16px;line-height:1.5}
.info svg{width:22px;height:22px;flex:none}

/* Footer */
.footer{top:3440px;height:52px;background:var(--black);color:#bbb;font-size:13px;display:flex;align-items:center;justify-content:center}
</style>
</head>
<body>

<header class="hero">
  <div class="hero-photo" role="img" aria-label="Bright modern interior with a curved glass wall and tall windows"></div>
  <div class="topbar">
    <div class="brand">
      <div class="brand-mark"></div>
      <div class="brand-name">Lumavane<span class="brand-tag">Window Treatment Solutions</span></div>
    </div>
    <ul class="nav">
      <li class="active">HOME</li><li>ABOUT</li><li>SERVICES</li><li>PRODUCTS</li><li>GALLERY</li><li>CONTACT</li>
    </ul>
  </div>
  <h1 class="hero-title">WINDOW<br>TREATMENT<br>SOLUTIONS</h1>
</header>

<section class="welcome">
  <h2>WELCOME TO<br><span>LUMAVANE</span></h2>
  <p>Lorem Ipsum is simply dummy text of the printing and typesetting industry. Lorem Ipsum has been the industry's standard dummy text ever since the 1500s, when an unknown printer took a galley of type and scrambled it to...</p>
  <div class="btn-outline">VIEW GALLERY
    <svg width="14" height="14" viewBox="0 0 14 14"><path d="M2 2l5 5-5 5M7 2l5 5-5 5" fill="none" stroke="#1c1c1c" stroke-width="2"/></svg>
  </div>
  <svg class="hex-cluster" viewBox="0 0 500 400" role="img" aria-label="Honeycomb of product photos: interior shades, outdoor screens and awnings">
    <g stroke="#fff" stroke-width="6">
      <polygon points="170,20 240,20 275,80 240,140 170,140 135,80" fill="#8e9699"/>
      <polygon points="340,20 410,20 445,80 410,140 340,140 305,80" fill="#59636b"/>
      <polygon points="65,140 135,140 170,200 135,260 65,260 30,200" fill="#a7adb0"/>
      <polygon points="220,140 290,140 325,200 290,260 220,260 185,200" fill="#f5f5f5"/>
      <polygon points="375,140 445,140 480,200 445,260 375,260 340,200" fill="#6b7b86"/>
      <polygon points="170,260 240,260 275,320 240,380 170,380 135,320" fill="#b08a5c"/>
      <polygon points="325,260 395,260 430,320 395,380 325,380 290,320" fill="#cfd3d5"/>
    </g>
    <circle cx="255" cy="200" r="34" fill="#2e2e2e"/>
  </svg>
</section>

<section class="products">
  <div class="product">
    <svg class="product-icon" viewBox="0 0 90 90"><circle cx="45" cy="45" r="42" fill="none" stroke="#2e2e2e" stroke-width="4"/><rect x="25" y="22" width="40" height="46" fill="none" stroke="#5cb531" stroke-width="4"/><path d="M25 32h40M25 42h40" stroke="#5cb531" stroke-width="3"/></svg>
    <div class="product-name">ROLLER<br><b>SHADES</b></div>
  </div>
  <div class="product">
    <svg class="product-icon" viewBox="0 0 90 90"><circle cx="45" cy="45" r="42" fill="none" stroke="#2e2e2e" stroke-width="4"/><path d="M24 22h42M28 22v46M62 22v46M28 22q10 24 0 46M62 22q-10 24 0 46" fill="none" stroke="#5cb531" stroke-width="3"/></svg>
    <div class="product-name">DRAPERY</div>
  </div>
  <div class="product">
    <svg class="product-icon" viewBox="0 0 90 90"><circle cx="45" cy="45" r="42" fill="none" stroke="#2e2e2e" stroke-width="4"/><rect x="24" y="24" width="42" height="42" fill="none" stroke="#5cb531" stroke-width="3"/><path d="M24 38h42M24 52h42M38 24v42M52 24v42" stroke="#5cb531" stroke-width="2"/></svg>
    <div class="product-name">OUTDOOR<br><b>BUG<br>SCREENS</b></div>
  </div>
  <div class="product">
    <svg class="product-icon" viewBox="0 0 90 90"><circle cx="45" cy="45" r="42" fill="none" stroke="#2e2e2e" stroke-width="4"/><path d="M22 30h46l-6 18H28z" fill="none" stroke="#5cb531" stroke-width="3"/><path d="M28 48v18M62 48v18" stroke="#5cb531" stroke-width="3"/></svg>
    <div class="product-name">AWNINGS</div>
  </div>
</section>

<section class="gallery">
  <h2>GALLERY</h2>
  <p class="lead">Lorem Ipsum is simply dummy text of the printing and typesetting industry.</p>
  <ul class="filters">
    <li class="active">All</li><li>ROLLER SHADES</li><li>DRAPERY</li><li>OUTDOOR BUG SCREENS</li><li>AWNINGS</li>
  </ul>
  <div class="grid">
    <div class="g1" role="img" aria-label="Patio with wooden roller blinds"></div>
    <div class="g2" role="img" aria-label="Glass roof pergola over terrace"></div>
    <div class="g3" role="img" aria-label="Modern retractable roof system"></div>
    <div class="g4" role="img" aria-label="Outdoor lounge under awning"></div>
    <div class="g5" role="img" aria-label="Louvered pergola structure"></div>
    <div class="g6" role="img" aria-label="Evening terrace with lit pergola"></div>
  </div>
</section>

<section class="why" role="img" aria-label="Dim interior of a workshop in the background">
  <h2>WHY<br>LUMAVANE?</h2>
  <p>Lorem Ipsum is simply dummy text of the printing and typesetting industry. Lorem Ipsum has been the industry's standard dummy text ever since the 1500s, when an unknown printer took a galley of type and scrambled it to make a type specimen book. It has survived not only five centuries, but also the leap into electronic typesetting, remaining essentially unchanged. It was popularised in the 1960s with the release of Letraset sheets containing Lorem Ipsum passages, and more recently with desktop publishing software like Aldus PageMaker including versions of Lorem Ipsum.</p>
  <div class="call">CALL US NOW!
    <svg class="call-icon" viewBox="0 0 54 54"><circle cx="27" cy="27" r="25" fill="none" stroke="#fff" stroke-width="3"/><path d="M19 16l5 0 2 6-3 2q3 6 9 9l2-3 6 2 0 5q-1 2-4 2q-17-2-19-19q0-3 2-4z" fill="#fff"/></svg>
    555-014-2290
  </div>
</section>

<section class="testimonial">
  <h2>CLIENT TESTIMONIAL</h2>
  <div class="quote-mark">&ldquo;</div>
  <svg class="arrow prev" viewBox="0 0 56 56"><circle cx="28" cy="28" r="25" fill="none" stroke="#333" stroke-width="2"/><path d="M32 18l-10 10 10 10" fill="none" stroke="#333" stroke-width="3"/></svg>
  <p>Lorem Ipsum is simply dummy text of the printing and typesetting industry. Lorem Ipsum has been the industry's standard dummy text ever since the 1500s, when an unknown printer took a galley of type and scrambled it to make a type specimen book.</p>
  <svg class="arrow next" viewBox="0 0 56 56"><circle cx="28" cy="28" r="25" fill="none" stroke="#333" stroke-width="2"/><path d="M24 18l10 10-10 10" fill="none" stroke="#333" stroke-width="3"/></svg>
  <div class="client">CLIENT NAME</div>
</section>

<svg class="scroll-badge" viewBox="0 0 100 100"><circle cx="50" cy="50" r="46" fill="#fff"/><circle cx="50" cy="50" r="36" fill="#2e2e2e"/><path d="M34 58l16-16 16 16" fill="none" stroke="#fff" stroke-width="6"/></svg>

<section class="contact">
  <div class="quote-form">
    <h3>GET A QUOTE</h3>
    <div class="row"><div class="field">Name</div><div class="field">Email</div></div>
    <div class="row"><div class="field">Subject</div></div>
    <div class="row"><div class="field tall">Message</div></div>
    <div class="submit">SUBMIT</div>
  </div>
  <div class="contact-side">
    <p class="intro">Lorem Ipsum is simply dummy text of the printing and typesetting industry.</p>
    <div class="contact-btn">CONTACT US</div>
    <h3>CONTACT INFO</h3>
    <ul class="info">
      <li><svg viewBox="0 0 22 22"><path d="M11 1a7 7 0 017 7c0 5-7 13-7 13S4 13 4 8a7 7 0 017-7z" fill="#fff"/><circle cx="11" cy="8" r="3" fill="#6f7773"/></svg><span>120 Harbour Lane, Toronto,<br>ON, M4B 1Z2<br>VIEW MAP</span></li>
      <li><svg viewBox="0 0 22 22"><path d="M5 2l4 0 1 5-2 2q2 4 6 6l2-2 5 1 0 4q-1 2-3 2Q3 19 2 5q0-3 3-3z" fill="#fff"/></svg><span>555-014-2290</span></li>
      <li><svg viewBox="0 0 22 22"><rect x="2" y="5" width="18" height="12" fill="none" stroke="#fff" stroke-width="2"/><path d="M2 5l9 7 9-7" fill="none" stroke="#fff" stroke-width="2"/></svg><span>Lorem ipsum is simply dummy</span></li>
    </ul>
  </div>
</section>

<footer class="footer">© LUMAVANE - 2016. All Rights Reserved.</footer>

</body>
</html>
```